Online Psychiatry business - Business Card

I need a business card design. The target audience is busy professionals of any field (this therapy appeals best to 24-35 year olds). It involves psychiatry by tele-medicine (or video-conference). Nothing on it should be a giveaway that it's about mental health. Professional design with silver or gold as the primary colors appeals to me. The card must be as simple and as uncluttered as possible. Some color and flowing design on the edge of the card appeals to me.
CalmHarborDirect.net should probably appear in the center of the card and stand out, i.e. bold lettering, and easy to read, no cursive, but Ariel Black. Some where below this, should appear "Too Busy to Take Care of Yourself? Think again." Since this isn't office based, I don't think an office address is necessary and limits clutter.
Information that does need to appear is my name: Gerald Mossvane, MD
General phone number: 555-417-8062. I'm hoping to get an 24-hour answering service soon so leave a little room for this. In addition I want to include two email addresses:
CalmHarborDirect@mailbox-example.net and CalmHarbor247@mailbox-example.net
Updates

I like the designs. I would like someone to put the website in bold in the center

 as most have been doing with a smaller font reminder nearby saying "No time" etc.
but I'd like to put my name down in the corner with the rest of the contact material.
Black print against a white or grey background appeals to me, with darker silver artwork near the sides (simple abstract, like wavy lines or something you can one up with that works. 
thanks

I ve tried to provide as much feedback as possible given my time limits, so if you have extra questions, please feel free to email. I tried to attach a file of a business card I really like but make be difficult to actually manufacture. I'm going to send you a link to the photo. The card has a pull tab. There is not much information on the outside. In fact, if you were to design the outside, I would just print : Too Busy to Take Care of Yourself? Think Again.

When you pull the tab the remaining information is on the bottom half of the card. Please don't use the color pink!!!!
http://www.cardgallery-example.org/2009/05/100-clever-print-ideas/
It is the 39th photo on the list, about 2/3ds of the way down the page. It is titled: Faltenkiste

#7 and #16 have an appeal to me, except for the dot patterns
Hope this helps

I'm running out of time and energy. I 've been trying to give do down the list and give  individual feedback but I won't be able to do that anymore.

So if you have any specific questions, write me, and again thank you for all your effort!!

I know i received your files, including your zip files, Pindrel,

but Milo, did you send me the files including ZIP on project 6143907?
thanks

Target Market(s)

Working professionals and executive, attorneys, etc.

Industry/Entity Type

Business

Logo Text

Don't Have Time to Take Care of Yourself? Think Again.

Logo styles of interest
Pictorial/Combination Logo
Wordmark Logo
Font styles to use
Other font styles liked:
• Ariel Black appeals to me the most

Requirements
Must have
• Want to emphasize that the website must be obvious, easily found (The CalmHarborDirect.net)
For that reason i'd like the card to be white, and minimal decoration on one or both sides just to add some style and color
Nice to have
• A Very uncluttered, elegant design, and something that makes it stick in your head-doesn't everyone want the last?
Should not have
• Nothing on the card that give it away that this is about psychiatry, such as brain or other symbol, but also nothing that gives it away as a medical business, such as a stethoscope or red cross or anything.

```html
<!DOCTYPE html>
<html lang="en">
<head>
<meta charset="utf-8">
<title>CalmHarborDirect.net – Business Card</title>
<link href="https://fonts.googleapis.com/css2?family=Arimo:wght@400;700&display=swap" rel="stylesheet">
<style>
  :root {
    --backdrop: #6b6b69;
    --card: #fbfbfb;
    --ink-soft: #8d8d8d;
    --ink-strong: #6a6a6a;
    --rule: #cfcfcf;
    --curve: #dcdcdc;
  }
  html, body {
    margin: 0;
    padding: 0;
    width: 1200px;
    height: 1000px;
    overflow: hidden;
    background: var(--backdrop);
    font-family: "Arimo", Arial, sans-serif;
  }
  .stage { position: relative; width: 1200px; height: 1000px; }
  .card {
    position: absolute;
    width: 520px;
    height: 300px;
    background: var(--card);
    box-shadow: 0 6px 18px rgba(0,0,0,0.25);
  }
  .card--front { left: 110px; top: 190px; }
  .card--back { left: 570px; top: 510px; }
  .card svg { display: block; width: 520px; height: 300px; }
  .tagline { font-size: 21px; fill: var(--ink-soft); }
  .tagline b, .tagline .strong { font-weight: 700; fill: var(--ink-strong); }
  .rule-dashed { stroke: var(--rule); stroke-width: 1.2; stroke-dasharray: 6 5; fill: none; }
  .rule-wave { stroke: var(--rule); stroke-width: 1.2; fill: none; }
  .edge-curve { stroke: var(--curve); stroke-width: 1.4; fill: none; }
  .pull-label { font-size: 8px; fill: var(--ink-soft); letter-spacing: 0.5px; }
  .name { font-size: 17px; font-weight: 700; fill: var(--ink-strong); }
  .phone { font-size: 16px; font-weight: 700; fill: var(--ink-strong); }
  .badge-ring { stroke: var(--ink-soft); stroke-width: 1.3; fill: none; }
  .badge-text { font-size: 7.5px; fill: var(--ink-strong); }
  .website { font-size: 14px; font-weight: 700; fill: var(--ink-strong); }
  .email { font-size: 11.5px; fill: var(--ink-soft); }
</style>
</head>
<body>
<main class="stage">

  <section class="card card--front" aria-label="Card front">
    <svg viewBox="0 0 520 300" xmlns="http://www.w3.org/2000/svg">
      <line class="rule-dashed" x1="90" y1="95" x2="520" y2="95"/>
      <text class="tagline" x="495" y="160" text-anchor="end">Too Busy to Take Care of Yourself? <tspan class="strong">Think again.</tspan></text>
      <path class="edge-curve" d="M0 168 Q20 192 90 195"/>
      <line class="rule-dashed" x1="90" y1="195" x2="520" y2="195"/>
      <path class="edge-curve" d="M90 195 Q40 198 38 240 Q40 282 90 285"/>
      <text class="pull-label" x="58" y="244" transform="rotate(90 58 244)" text-anchor="middle">PULL</text>
      <path class="edge-curve" d="M0 258 Q20 284 90 285"/>
    </svg>
  </section>

  <section class="card card--back" aria-label="Card back">
    <svg viewBox="0 0 520 300" xmlns="http://www.w3.org/2000/svg">
      <path class="rule-wave" d="M120 70 q13 -4 26 0 t26 0 t26 0 t26 0 t26 0 t26 0 t26 0 t26 0 t26 0 t26 0 t26 0 t26 0 t26 0 t26 0 t26 0 t26 0"/>
      <text class="tagline" x="495" y="118" text-anchor="end">Too Busy to Take Care of Yourself? <tspan class="strong">Think again.</tspan></text>
      <path class="edge-curve" d="M0 118 Q20 140 90 142"/>
      <path class="rule-wave" d="M90 142 q13 -4 26 0 t26 0 t26 0 t26 0 t26 0 t26 0 t26 0 t26 0 t26 0 t26 0 t26 0 t26 0 t26 0 t26 0 t26 0 t26 0 t26 0"/>
      <text class="name" x="38" y="182">GERALD MOSSVANE, MD</text>
      <text class="phone" x="70" y="218">call 555-417-8062</text>
      <circle class="badge-ring" cx="228" cy="212" r="11"/>
      <text class="badge-text" x="228" y="215" text-anchor="middle">24/7</text>
      <text class="website" x="270" y="170">CalmHarborDirect.net</text>
      <text class="email" x="270" y="190">CalmHarbor247@mailbox-example.net</text>
      <text class="email" x="270" y="207">CalmHarborDirect@mailbox-example.net</text>
      <path class="rule-wave" d="M90 248 q13 -4 26 0 t26 0 t26 0 t26 0 t26 0 t26 0 t26 0 t26 0 t26 0 t26 0 t26 0 t26 0 t26 0 t26 0 t26 0 t26 0 t26 0"/>
      <path class="edge-curve" d="M0 225 Q20 246 90 248"/>
    </svg>
  </section>

</main>
</body>
</html>
```